Private Investment Firm Needs PowerPoint Presentation Template

Design PowerPoint template, take Pinebrook-submitted rough presentation draft, and drop it into new template. See attached Project Brief file for more detail.
Updates

Some decent designs have been submitted but they seem to lack the understanding of our target markets. I am hopeful that more time and feedback will result in better results.

Target Market(s)

Private company owners and intermediaries.

Font styles to use
Serif

Colors
3176b5

Requirements
Must have
• See attached Project Brief.
Nice to have
Should not have
• No B2C fluff--this is a B2B project.

```html
<!DOCTYPE html>
<html lang="en">
<head>
<meta charset="utf-8">
<title>Introduction to Non-Control Capital – Template Slides</title>
<link rel="stylesheet" href="https://fonts.googleapis.com/css2?family=Cormorant+SC:wght@500;600&family=Montserrat:wght@400;500;600;700&family=Open+Sans:wght@400;600&display=swap">
<style>
:root{
  --page:#b4b4b4;
  --blue:#3176b5;
  --blue-deep:#0d5aa7;
  --navy:#0b3c73;
  --ink:#4a4d52;
  --slate:#54575c;
  --cyan:#4ec3ea;
  --rule:#d9dbde;
}
*{margin:0;padding:0;box-sizing:border-box}
html,body{width:1043px;height:1200px;overflow:hidden}
body{background:radial-gradient(ellipse at 50% 40%,#cfcfcf 0%,var(--page) 75%,#a5a5a5 100%);font-family:"Open Sans",Arial,sans-serif;color:var(--ink);position:relative}
.slide{position:absolute;width:444px;height:249px;overflow:hidden;background:linear-gradient(160deg,#ffffff 0%,#f4f5f6 55%,#e6e8ea 100%);box-shadow:0 2px 6px rgba(0,0,0,.28)}
.s1{left:50px;top:52px}.s2{left:545px;top:52px}
.s3{left:50px;top:341px}.s4{left:545px;top:341px}
.s5{left:50px;top:616px}.s6{left:545px;top:616px}
.s7{left:50px;top:900px}.s8{left:545px;top:900px}
.frame{position:absolute;inset:0;width:444px;height:249px}
.content{position:absolute;inset:0}
.footer-brand{position:absolute;left:20px;top:219px;display:flex;align-items:center;gap:4px;font-family:"Montserrat",sans-serif;font-weight:600;font-size:7px;letter-spacing:.8px;color:var(--navy)}
.footer-brand i{width:10px;height:10px;border-radius:50%;background:var(--navy);display:block}
.footer-url{position:absolute;left:230px;top:222px;font-family:"Montserrat",sans-serif;font-size:6.2px;color:#333}
.footer-url b{color:var(--blue-deep);font-weight:600}
.page-num{position:absolute;left:405px;top:222px;font-family:"Montserrat",sans-serif;font-size:5.5px;font-weight:700;color:#fff}
.heading{position:absolute;left:40px;right:40px;text-align:center;font-family:"Montserrat",sans-serif;font-weight:700;color:var(--blue-deep);font-size:13.5px}
.heading::after{content:"";display:block;width:20px;height:1.5px;background:var(--blue-deep);margin:5px auto 0}
.bullets{position:absolute;list-style:none;font-size:6.6px;line-height:1.3}
.bullets>li{position:relative;padding-left:12px;margin-bottom:7px}
.bullets>li::before{content:"";position:absolute;left:2px;top:3px;width:3px;height:3px;border-radius:50%;background:var(--blue-deep)}
.ticks{list-style:none;margin-top:3px}
.ticks li{position:relative;padding-left:9px;margin-bottom:6px}
.ticks li::before{content:"✓";position:absolute;left:0;top:0;color:var(--blue-deep);font-size:6px}
.bold li{font-weight:600;color:#3c3f44}
.bold .ticks li{font-weight:400}
.nowrap{white-space:nowrap}

/* title slide */
.cover-title{position:absolute;left:77px;width:290px;top:46px;text-align:center;white-space:nowrap;font-family:"Cormorant SC",serif;font-weight:600;font-size:25px;line-height:24px;color:var(--blue-deep)}
.cover-sub{position:absolute;left:110px;width:224px;top:103px;text-align:center;font-size:5.8px;line-height:1.45;color:#666}
.cover-sub b{color:var(--blue-deep)}
.cover-season{position:absolute;left:173px;top:143px;width:101px;height:26px;border:1px solid #777;display:flex;align-items:center;justify-content:center;font-family:"Montserrat",sans-serif;font-size:14px;color:#444}
.cover-brand{position:absolute;left:180px;top:192px;display:flex;align-items:center;gap:5px;font-family:"Montserrat",sans-serif;font-weight:600;font-size:10px;letter-spacing:1px;color:var(--navy)}
.cover-brand i{width:15px;height:15px;border-radius:50%;background:var(--navy);display:block}
.cover-url{position:absolute;left:157px;top:232px;font-family:"Montserrat",sans-serif;font-size:9.5px;color:#222}
.cover-url b{color:var(--blue-deep);font-weight:600}

/* quote slide */
.quote-mark{position:absolute;font-family:Georgia,serif;font-size:56px;color:#c9cbcf;line-height:1}
.quote-text{position:absolute;left:94px;top:69px;width:224px;font-family:"Montserrat",sans-serif;font-size:10.2px;line-height:11.6px;color:#4b4e53}
.quote-cite{position:absolute;left:144px;top:173px;font-family:"Montserrat",sans-serif;font-size:6px;font-weight:600;color:var(--blue-deep)}

/* uses grid */
.uses{position:absolute;left:55px;top:57px;display:grid;grid-template-columns:repeat(4,83px);grid-template-rows:repeat(3,49px);gap:1.5px}
.use{background:linear-gradient(180deg,#f3f4f5,#e3e5e7);text-align:center;padding:4px 4px 0;box-shadow:0 1px 2px rgba(0,0,0,.12)}
.use h4{font-family:"Montserrat",sans-serif;font-size:5.6px;font-weight:700;color:var(--blue-deep);line-height:1.15;margin-bottom:2px}
.use p{font-size:3.6px;line-height:1.3;color:#666}

/* capital stack */
.banner{position:absolute;left:56px;top:21px;width:316px;height:24px;background:var(--blue-deep);color:#fff;font-family:"Cormorant SC",serif;font-weight:600;font-size:15px;display:flex;align-items:center;justify-content:center;letter-spacing:.5px;transform:skewX(-10deg)}
.banner span{transform:skewX(10deg)}
.stack-bar{position:absolute;left:50px;top:52px;width:323px;height:14px;background:var(--cyan);font-family:"Montserrat",sans-serif;font-weight:700;font-size:6.5px;color:#0b2b50;display:flex;align-items:center;justify-content:center}
.tier{position:absolute;left:50px;width:101px}
.tier .label{background:var(--blue-deep);color:#fff;font-family:"Montserrat",sans-serif;font-weight:700;font-size:6.5px;text-align:center;height:11px;line-height:11px}
.tier .item{font-size:4.2px;text-align:center;height:11px;line-height:11px;color:#444;border-bottom:1px solid var(--rule);background:#f1f2f3}
.panel{position:absolute;left:153px;width:220px;color:#fff;text-align:center;font-size:4.4px;line-height:1.35;display:flex;flex-direction:column;justify-content:center;padding:0 10px}
.panel h5{font-family:"Montserrat",sans-serif;font-size:5px;font-weight:700}
.divider{position:absolute;left:50px;top:151px;width:323px;height:3px;background:repeating-linear-gradient(90deg,var(--blue-deep) 0 46px,#ffffff 46px 48px)}

/* balance sheet */
.sheet{position:absolute;left:57px;top:63px;width:330px;table-layout:fixed;border-collapse:collapse;font-size:6.2px;color:#555}
.sheet th{background:var(--blue-deep);color:#fff;text-align:left;font-family:"Montserrat",sans-serif;font-size:6.4px;font-weight:700;height:12px;padding-left:10px}
.sheet td{height:13px;padding-left:10px;background:linear-gradient(180deg,#f6f7f8,#e8eaec)}
.sheet td.gap,.sheet th.gap{background:#a9abae;padding:0}
.sheet .hi{background:var(--cyan);color:#fff}
.sheet .hi-deep{background:var(--blue-deep);color:#fff}
</style>
</head>
<body>

<!-- 1 · Cover -->
<section class="slide s1">
  <svg class="frame" viewBox="0 0 444 249" aria-hidden="true">
    <defs><linearGradient id="edge1" x1="0" y1="0" x2="0" y2="1"><stop offset="0" stop-color="#1c7ed0"/><stop offset="1" stop-color="#0d5aa7"/></linearGradient></defs>
    <polygon points="0,0 48,0 0,108" fill="#54575c"/>
    <polygon points="419,0 444,0 444,249 362,249" fill="url(#edge1)"/>
  </svg>
  <div class="content">
    <h1 class="cover-title">Introduction to<br>Non-Control Capital</h1>
    <p class="cover-sub">The Lower Middle Market Private Company Strategy for<br>Raising Capital While <b>Maintaining Business Control</b></p>
    <div class="cover-season">Fall-2018</div>
    <div class="cover-brand"><i></i>PINEBROOK</div>
    <div class="cover-url">www.<b>pinebrookcapital</b>.com</div>
  </div>
</section>

<!-- 2 · Introduction -->
<section class="slide s2">
  <svg class="frame" viewBox="0 0 444 249" aria-hidden="true">
    <defs><linearGradient id="edge2" x1="0" y1="0" x2="0" y2="1"><stop offset="0" stop-color="#1c7ed0"/><stop offset="1" stop-color="#0d5aa7"/></linearGradient></defs>
    <polygon points="0,0 48,0 0,108" fill="#54575c"/>
    <polygon points="419,0 444,0 444,249 362,249" fill="url(#edge2)"/>
  </svg>
  <div class="content">
    <h2 class="heading" style="top:30px;font-size:13px">INTRODUCTION</h2>
    <ul class="bullets" style="left:46px;top:62px;width:320px">
      <li>Private company owners have traditionally considered two capital raising options
        <ul class="ticks"><li>Borrow from a local bank, or</li><li>Sell most or all of the company to a change- of-control investor (aka Buyout firm)</li></ul></li>
      <li>An alternative most have not considered is the raising of Non-Control Capital, orcapital that is invested into the business yet allows those same owners to retaincontrolling interest in their company</li>
      <li>Non-Control Capital is not appropriate for every private company owner but neither is a Change-of-Control sale</li>
      <li>The key is to determine what the business and owners require, and then partner withan investor best aligned with those needs so that long-term company growth, and personal goals, can both be achieved</li>
    </ul>
    <div class="footer-brand"><i></i>PINEBROOK</div>
    <div class="footer-url">www.<b>pinebrookcapital</b>.com</div>
    <div class="page-num">2.</div>
  </div>
</section>

<!-- 3 · Definition -->
<section class="slide s3">
  <svg class="frame" viewBox="0 0 444 249" aria-hidden="true">
    <defs><linearGradient id="edge3" x1="0" y1="0" x2="0" y2="1"><stop offset="0" stop-color="#1c7ed0"/><stop offset="1" stop-color="#0d5aa7"/></linearGradient></defs>
    <polygon points="0,0 48,0 0,108" fill="#54575c"/>
    <polygon points="419,0 444,0 444,249 362,249" fill="url(#edge3)"/>
  </svg>
  <div class="content">
    <h2 class="heading" style="top:29px">What is Non-Control Capital?</h2>
    <ul class="bullets bold nowrap" style="left:47px;top:67px;width:300px">
      <li>Non-Control Capital is an investment which is primarily used for the ongoing operation<br>and/or growth of a business but also allows the current owners to retain:
        <ul class="ticks" style="margin-top:8px"><li>Control of the business economics</li><li>Control of the business operations</li><li>Control of strategy and key decision making</li><li>Control of the Board of Directors</li></ul></li>
      <li>Requires the alignment of management incentives with ownership</li>
      <li>In essence, a company receives the capital it needs to implement its business<br>plans but owners continue to retain ultimate control</li>
    </ul>
    <div class="footer-brand"><i></i>PINEBROOK</div>
    <div class="footer-url">www.<b>pinebrookcapital</b>.com</div>
    <div class="page-num">3.</div>
  </div>
</section>

<!-- 4 · Fit -->
<section class="slide s4">
  <svg class="frame" viewBox="0 0 444 249" aria-hidden="true">
    <defs><linearGradient id="edge4" x1="0" y1="0" x2="0" y2="1"><stop offset="0" stop-color="#1c7ed0"/><stop offset="1" stop-color="#0d5aa7"/></linearGradient></defs>
    <polygon points="0,0 48,0 0,108" fill="#54575c"/>
    <polygon points="419,0 444,0 444,249 362,249" fill="url(#edge4)"/>
  </svg>
  <div class="content">
    <h2 class="heading" style="top:29px;left:20px;right:20px">When is a Non-Control Transaction Appropriate?</h2>
    <ul class="bullets bold" style="left:46px;top:71px;width:330px">
      <li style="margin-bottom:5px">The company has opportunities to expand but requires capital to do so</li>
      <li style="margin-bottom:5px">At least one active owner is not close to retirement</li>
      <li style="margin-bottom:5px">The company is not in a turnaround situation</li>
      <li style="margin-bottom:5px">Family members may work in the business and want to continue</li>
      <li style="margin-bottom:5px">Owners care about keeping the business in their family name (legacy)</li>
      <li style="margin-bottom:5px">Liquidity (dividend) is not the major use of the invested capital</li>
      <li style="margin-bottom:5px">Owners are sensitive to utilizing too much debt</li>
      <li style="margin-bottom:5px">Companies require more than just capital:</li>
      <li style="margin-bottom:5px">They may also need operational, marketing, financial, and/or technology counsel</li>
    </ul>
    <div class="footer-brand"><i></i>PINEBROOK</div>
    <div class="footer-url">www.<b>pinebrookcapital</b>.com</div>
    <div class="page-num">4.</div>
  </div>
</section>

<!-- 5 · Testimonial -->
<section class="slide s5">
  <svg class="frame" viewBox="0 0 444 249" aria-hidden="true">
    <defs><linearGradient id="edge5" x1="0" y1="0" x2="0" y2="1"><stop offset="0" stop-color="#1c7ed0"/><stop offset="1" stop-color="#0d5aa7"/></linearGradient></defs>
    <polygon points="0,0 48,0 0,108" fill="#54575c"/>
    <polygon points="419,0 444,0 444,249 362,249" fill="url(#edge5)"/>
  </svg>
  <div class="content">
    <div class="quote-mark" style="left:94px;top:26px">“</div>
    <p class="quote-text">Our company had several business opportunities but I needed outside capital to take advantage of them. Why would I cede control of my business when we were at the exact point when raising outside capital would allow me to accelerate growth and achieve my life-long business and personal goals?!</p>
    <div class="quote-cite">--Daniel Harlow, CEO; The Ridgeline Group</div>
    <div class="quote-mark" style="left:290px;top:172px">”</div>
    <div class="footer-brand"><i></i>PINEBROOK</div>
    <div class="footer-url">www.<b>pinebrookcapital</b>.com</div>
    <div class="page-num">5.</div>
  </div>
</section>

<!-- 6 · Uses -->
<section class="slide s6">
  <svg class="frame" viewBox="0 0 444 249" aria-hidden="true">
    <defs><linearGradient id="edge6" x1="0" y1="0" x2="0" y2="1"><stop offset="0" stop-color="#1c7ed0"/><stop offset="1" stop-color="#0d5aa7"/></linearGradient></defs>
    <polygon points="0,0 48,0 0,108" fill="#54575c"/>
    <polygon points="419,0 444,0 444,249 362,249" fill="url(#edge6)"/>
  </svg>
  <div class="content">
    <h2 class="heading" style="top:27px;font-size:13px">The 12 Primary Uses of Non-Control Capital</h2>
    <div class="uses">
      <div class="use"><h4>Growth</h4><p>Capital used to expand, add products, or hire staff</p></div>
      <div class="use"><h4>Acquisitions</h4><p>Capital used to acquire one or more competitors</p></div>
      <div class="use"><h4>Partner or Shareholder Buy-Out</h4><p>Capital used to buy out an inactive partner</p></div>
      <div class="use"><h4>Management Buy-Out (MBO)</h4><p>When management buys most or all of the owners</p></div>
      <div class="use"><h4>Management Buy-In (MBI)</h4><p>When outside executives buy a business and need capital</p></div>
      <div class="use"><h4>Family Ownership &amp; Wealth Transfer</h4><p>When junior generations acquire senior family ownership interests</p></div>
      <div class="use"><h4>Balance Sheet Recapitalization</h4><p>Changes the debt and equity mix of a company</p></div>
      <div class="use"><h4>Refinancing</h4><p>Replacing one form of debt with better terms</p></div>
      <div class="use"><h4>Family Office Support</h4><p>Allows a family office to invest alongside a junior provider</p></div>
      <div class="use"><h4>Senior Lender Enhancement or Transition</h4><p>When a company outgrows its senior bank lender</p></div>
      <div class="use"><h4>De-Lever Balance Sheet</h4><p>When a company has too much debt and needs flexibility</p></div>
      <div class="use"><h4>Owner Dividend (Liquidity)</h4><p>When owners take a one-time distribution to diversify</p></div>
    </div>
    <div class="footer-brand"><i></i>PINEBROOK</div>
    <div class="footer-url">www.<b>pinebrookcapital</b>.com</div>
    <div class="page-num">6.</div>
  </div>
</section>

<!-- 7 · Capital stack -->
<section class="slide s7">
  <svg class="frame" viewBox="0 0 444 249" aria-hidden="true">
    <defs><linearGradient id="edge7" x1="0" y1="0" x2="0" y2="1"><stop offset="0" stop-color="#1c7ed0"/><stop offset="1" stop-color="#0d5aa7"/></linearGradient></defs>
    <polygon points="0,0 48,0 0,108" fill="#54575c"/>
    <polygon points="419,0 444,0 444,249 362,249" fill="url(#edge7)"/>
    <polygon points="58,21 66,21 60,45 52,45" fill="#3c3f44"/>
    <polygon points="364,21 372,21 366,45 358,45" fill="#3c3f44"/>
  </svg>
  <div class="content">
    <div class="banner"><span>Pinebrook Provides Junior Capital</span></div>
    <div class="stack-bar">Capital Stack Hierarchy.</div>
    <div class="tier" style="top:71px">
      <div class="label">Senior Debt</div>
      <div class="item">Revolver</div>
      <div class="item">Asset-Based Loan</div>
      <div class="item">Senior Term Loan</div>
      <div class="label">Combination</div>
      <div class="item">Unitranche</div>
    </div>
    <div class="panel" style="top:71px;height:73px;background:var(--blue-deep)">
      <h5>Senior Debt Capital Providers</h5>
      <p>Paid back first, plays more of a lender than partner role, less value-added, less equity dilutive, less expensive capital, but not strategically focused</p>
    </div>
    <div class="divider"></div>
    <div class="tier" style="top:158px">
      <div class="label">Junior Capital</div>
      <div class="item">Subordinated Debt</div>
      <div class="item">Preferred Stock</div>
      <div class="item">Common Stock</div>
    </div>
    <div class="panel" style="top:158px;height:51px;background:#0a2440">
      <h5>What Pinebrook Invests</h5>
      <p>Sits junior to all other capital (taking on more risk), plays a partner role, more value-added services provided, more expensive than senior debt, but supplies an engine for continuous improvement and growth</p>
    </div>
    <div class="footer-brand"><i></i>PINEBROOK</div>
    <div class="footer-url">www.<b>pinebrookcapital</b>.com</div>
    <div class="page-num">7.</div>
  </div>
</section>

<!-- 8 · Balance sheet -->
<section class="slide s8">
  <svg class="frame" viewBox="0 0 444 249" aria-hidden="true">
    <defs><linearGradient id="edge8" x1="0" y1="0" x2="0" y2="1"><stop offset="0" stop-color="#1c7ed0"/><stop offset="1" stop-color="#0d5aa7"/></linearGradient></defs>
    <polygon points="0,0 48,0 0,108" fill="#54575c"/>
    <polygon points="419,0 444,0 444,249 362,249" fill="url(#edge8)"/>
  </svg>
  <div class="content">
    <h2 class="heading" style="top:24px;left:60px;right:60px;font-size:13px;line-height:16px">A Balance Sheet: Pinebrook’s Position in the Capital Stack</h2>
    <table class="sheet">
      <colgroup><col style="width:110px"><col style="width:42px"><col style="width:178px"></colgroup>
      <tr><th>Assets</th><th class="gap"></th><th>Liabilities</th></tr>
      <tr><td>Cash</td><td class="gap"></td><td>Accounts Payable</td></tr>
      <tr><td>Marketable Securities</td><td class="gap"></td><td>Taxes Payable</td></tr>
      <tr><td>Accounts Receivable</td><td class="gap"></td><td>Revolver</td></tr>
      <tr><td>Inventory</td><td class="gap"></td><td>Senior Term Loan</td></tr>
      <tr><td>PP&amp;E</td><td class="gap"></td><td>Unitranche Debt</td></tr>
      <tr><td>Intangible Assets</td><td class="gap"></td><td class="hi">Subordinated Debt*</td></tr>
      <tr><td>Other Assets</td><td class="gap"></td><td class="hi-deep">Equity</td></tr>
      <tr><td></td><td class="gap"></td><td>Owners’ Equity</td></tr>
      <tr><td></td><td class="gap"></td><td class="hi">Preferred Stock</td></tr>
      <tr><td></td><td class="gap"></td><td class="hi">Common Stock</td></tr>
    </table>
    <div class="footer-brand"><i></i>PINEBROOK</div>
    <div class="footer-url">www.<b>pinebrookcapital</b>.com</div>
    <div class="page-num">8.</div>
  </div>
</section>

</body>
</html>
```